Luxury Toilet Rental Business. Tallowby Hire.

Tallowby Hire (the logo is in the uploaded files)
We RENT and SELL Luxury Trailer toilets.
- Show location, number, pricing, pictures.
- We have two stall trailers for rent AND 3 stall trailers
- We sell them too
- We want our phone number shown
- We are a local company
- Slogan: Brighten your gathering with Tallowby Hire. The Velvet Privy
- We want a pricing portion
- We want the sizes shown
- We want the different rates/ prices shown
- We do 1 day rentals
- We do 1 week rentals
- We want the service area. We serve Los Angeles County, Orange County, Riverside County, San Bernardino County, and Palm Desert.
- Our location is in Corvell Park, CA

Target Market(s)

Event planners, wedding planners, venue planners, concerts, events, gatherings.

Industry/Entity Type

Luxury Toilet Rentals

Number of Pages Required

1 page

Font styles to use
Serif
Sans Serif

Colors
EE7325
F08F49
F5BC92
FAE3D3
FDF4ED

Requirements
Must have
• Location, pricing, pictures, available areas. Our slogan.
Nice to have
• I like the idea of having tabs that show price, a tab that shows our contact information, pictures, event ideas, and where we service (the areas we'll go to)

```html
<!DOCTYPE html>
<html lang="en">
<head>
<meta charset="utf-8">
<title>Tallowby Hire – Landing page mobile view</title>
<link rel="stylesheet" href="https://fonts.googleapis.com/css2?family=Inter:wght@400;500;600;700&display=swap">
<style>
  :root {
    --orange: #EE7325;
    --orange-mid: #F08F49;
    --orange-soft: #F5BC92;
    --peach: #FAE3D3;
    --cream: #FDF4ED;
    --ink: #1d1d1f;
    --grey: #6b6b6b;
    --muted: #a8a8a8;
    --line: #e6e0db;
    --white: #ffffff;
    --photo-dark: #6f7376;
    --photo-light: #c9cdd0;
  }
  * { box-sizing: border-box; margin: 0; padding: 0; }
  html, body { width: 1200px; height: 900px; overflow: hidden; background: var(--white); }
  body { position: relative; font-family: "Inter", Arial, sans-serif; color: var(--ink); }

  /* Intro */
  .intro { position: absolute; left: 78px; top: 187px; }
  .brand-mark { display: flex; align-items: center; gap: 8px; height: 50px; }
  .brand-mark .square { width: 26px; height: 26px; background: var(--orange); }
  .brand-mark .name { font-size: 29px; font-weight: 700; color: var(--orange); letter-spacing: .2px; }
  .intro-title { margin-top: 48px; font-size: 29px; font-weight: 600; }
  .intro-sub { margin-top: 12px; font-size: 21px; color: #444; }

  /* Screens */
  .screen { position: absolute; width: 205px; background: var(--white); border-radius: 14px;
    overflow: hidden; box-shadow: 0 2px 10px rgba(0,0,0,.10); border: 1px solid #eee; }
  .abs { position: absolute; }
  .photo { background: linear-gradient(160deg, var(--photo-light), var(--photo-dark)); }
  .orange { color: var(--orange); }
  .btn-fill { background: var(--orange); color: var(--white); border-radius: 3px; font-size: 6px;
    display: flex; align-items: center; justify-content: center; font-weight: 600; }
  .btn-line { border: 1px solid var(--orange); color: var(--orange); border-radius: 4px;
    display: flex; align-items: center; justify-content: center; font-weight: 500; background: var(--white); }
  .chip { background: var(--white); border-radius: 6px; font-size: 5px; padding: 2px 5px; color: var(--grey); white-space: nowrap; }

  /* Home page pieces */
  .page-band { left: 0; top: 0; width: 100%; height: 367px; background: var(--cream); }
  .mini-brand { left: 9px; top: 10px; display: flex; align-items: center; gap: 3px; }
  .mini-brand .square { width: 8px; height: 8px; background: var(--orange); }
  .mini-brand .name { font-size: 8px; font-weight: 700; color: var(--orange); }
  .menu-dot { right: 9px; top: 11px; width: 17px; height: 17px; border-radius: 50%; background: var(--orange); }
  .search-ico { right: 32px; top: 14px; }
  .headline { left: 9px; top: 46px; width: 190px; font-size: 12.5px; line-height: 1.3; font-weight: 700; color: var(--orange); }
  .hero-strip { left: 97px; top: 103px; width: 109px; height: 48px; }
  .finder-label { left: 9px; top: 138px; font-size: 7px; font-weight: 600; color: var(--orange); }
  .finder { left: 9px; top: 153px; width: 188px; height: 200px; background: var(--white); border: 1px solid var(--line); border-radius: 4px; }
  .field-label { position: absolute; left: 10px; font-size: 6.5px; color: var(--ink); }
  .field { position: absolute; left: 10px; width: 168px; height: 20px; background: var(--cream); border-radius: 3px;
    display: flex; align-items: center; gap: 6px; padding-left: 7px; font-size: 6px; color: var(--muted); }
  .filter-row { position: absolute; left: 10px; top: 142px; display: flex; gap: 4px; align-items: center; font-size: 6px; }
  .pill { border: 1px solid var(--orange-mid); color: var(--orange); border-radius: 7px; padding: 1px 5px; font-size: 5.5px; }
  .search-btn { position: absolute; left: 10px; top: 160px; width: 168px; height: 21px; font-size: 8px; }
  .perk-tick { left: 9px; }
  .perk-title { left: 9px; font-size: 7px; font-weight: 600; color: var(--orange); }
  .perk-text { left: 9px; width: 130px; font-size: 6px; line-height: 1.4; color: var(--orange-mid); }

  /* Options screen */
  .options-band { left: 0; top: 0; width: 100%; height: 348px; background: var(--cream); }
  .section-title { left: 0; width: 100%; text-align: center; font-size: 11px; font-weight: 700; color: var(--orange); }
  .offer-card { left: 9px; width: 187px; height: 144px; background: var(--white); border-radius: 4px; }
  .offer-photo { position: absolute; left: 5px; top: 9px; width: 177px; height: 70px; }
  .offer-badges { position: absolute; left: 9px; top: 68px; display: flex; gap: 3px; }
  .offer-name { position: absolute; left: 8px; top: 89px; font-size: 7px; font-weight: 600; color: var(--orange); }
  .offer-feats { position: absolute; left: 8px; top: 101px; display: flex; gap: 7px; font-size: 4.5px; color: var(--grey); }
  .offer-btn { position: absolute; left: 8px; top: 119px; width: 171px; height: 14px; font-size: 5.5px; }
  .feat-title { left: 9px; top: 365px; font-size: 10px; font-weight: 700; color: var(--orange); }
  .explore { left: 9px; top: 385px; width: 78px; height: 24px; font-size: 7.5px; }
  .area-label { left: 9px; top: 433px; font-size: 6.5px; color: var(--orange); font-weight: 500; }
  .area-select { left: 9px; top: 446px; width: 140px; height: 20px; background: var(--cream); border-radius: 3px;
    display: flex; align-items: center; gap: 5px; padding-left: 7px; font-size: 6px; color: var(--muted); }

  /* Product screen */
  .product-card { left: 0; top: 0; width: 100%; height: 305px; background: var(--cream); }
  .product-photo { left: 7px; top: 10px; width: 191px; height: 165px; border-radius: 3px; }
  .price-tag { left: 7px; top: 160px; background: var(--white); border-radius: 10px; padding: 4px 10px; font-size: 9px; color: var(--ink); }
  .product-name { left: 18px; top: 213px; font-size: 15px; font-weight: 600; color: var(--orange); }
  .product-size { left: 18px; top: 236px; font-size: 10px; color: var(--orange-mid); }
  .book-btn { left: 18px; top: 261px; width: 162px; height: 30px; font-size: 10px; }
  .next-photo { left: 7px; top: 315px; width: 191px; height: 120px; border-radius: 3px; }

  /* Contact screen */
  .location-band { left: 0; top: 0; width: 100%; height: 285px; background: var(--cream); }
  .location-photo { left: 99px; top: 0; width: 106px; height: 285px; background: linear-gradient(200deg, #d9d6cf 0%, #7c7a76 45%, #2a2a2a 100%); }
  .loc-title { left: 9px; top: 62px; font-size: 11px; font-weight: 600; color: var(--orange); }
  .loc-sub { left: 9px; top: 78px; font-size: 6px; color: var(--orange-mid); }
  .map-btn { left: 9px; top: 98px; width: 78px; height: 24px; font-size: 7.5px; }
  .newsletter { left: 9px; top: 302px; width: 188px; height: 81px; background: var(--orange); border-radius: 4px; }
  .newsletter h3 { position: absolute; left: 10px; top: 13px; font-size: 7px; font-weight: 600; color: var(--white); }
  .newsletter p { position: absolute; left: 10px; top: 25px; width: 150px; font-size: 5.5px; line-height: 1.4; color: var(--white); }
  .news-input { position: absolute; left: 10px; top: 50px; width: 168px; height: 14px; background: var(--white); border-radius: 7px;
    font-size: 5.5px; color: var(--muted); display: flex; align-items: center; padding-left: 8px; }
  .news-btn { position: absolute; right: 2px; top: 2px; height: 10px; width: 32px; border-radius: 5px; background: var(--orange); color: var(--white);
    font-size: 5px; display: flex; align-items: center; justify-content: center; }
  .foot-brand { left: 9px; top: 400px; display: flex; align-items: center; gap: 4px; }
  .foot-brand .square { width: 11px; height: 11px; background: var(--orange); }
  .foot-brand .name { font-size: 11px; font-weight: 700; color: var(--orange); }
  .foot-slogan { left: 9px; top: 432px; width: 150px; font-size: 6px; line-height: 1.45; color: var(--ink); }
  .contact-row { left: 9px; display: flex; gap: 9px; align-items: flex-start; }
  .contact-row .lbl { font-size: 6px; color: var(--ink); }
  .contact-row .val { font-size: 6px; color: var(--orange); margin-top: 2px; }
  .accordion { left: 9px; width: 187px; }
  .acc-row { height: 20.5px; border-bottom: 1px solid #cfcfcf; display: flex; justify-content: space-between; align-items: center;
    font-size: 6.5px; font-weight: 600; }
  .acc-row span:last-child { color: var(--muted); font-weight: 400; }
  .foot-links { left: 9px; top: 693px; list-style: none; font-size: 6px; line-height: 15px; }
  .copyright { left: 9px; top: 775px; font-size: 5.5px; color: var(--ink); }
</style>
</head>
<body>

<section class="intro">
  <div class="brand-mark"><span class="square"></span><span class="name">Tallowby Hire</span></div>
  <h1 class="intro-title">Tallowby Hire</h1>
  <p class="intro-sub">Landing page mobile view</p>
</section>

<!-- Home screen, scrolled -->
<div class="screen" style="left:465px; top:-136px; height:496px;">
  <div class="abs page-band"></div>
  <div class="abs photo hero-strip" role="img" aria-label="Luxury restroom trailer at an event"></div>
  <span class="abs chip" style="left:150px; top:136px">Luxury Trailer Tours</span>
  <div class="abs finder-label">Find your Trailer</div>
  <form class="abs finder">
    <span class="field-label" style="top:8px">Where do you need your Trailers?</span>
    <div class="field" style="top:18px"><svg width="8" height="9" viewBox="0 0 8 10"><path d="M4 9.5S.8 6 .8 3.8a3.2 3.2 0 0 1 6.4 0C7.2 6 4 9.5 4 9.5z" fill="none" stroke="#EE7325" stroke-width="1"/><circle cx="4" cy="3.8" r="1.1" fill="#EE7325"/></svg>Los Angeles County</div>
    <span class="field-label" style="top:49px">When do you need?</span>
    <div class="field" style="top:59px"><svg width="8" height="8" viewBox="0 0 8 8"><rect x=".5" y="1.2" width="7" height="6.3" rx="1" fill="none" stroke="#EE7325"/><path d="M.5 3h7M2.3.3v1.6M5.7.3v1.6" stroke="#EE7325"/></svg>Pick a Date</div>
    <span class="field-label" style="top:92px">How much do you need?</span>
    <div class="field" style="top:102px"><svg width="8" height="8" viewBox="0 0 8 8"><circle cx="3.2" cy="2.4" r="1.8" fill="none" stroke="#EE7325"/><path d="M.4 7.6c.4-1.8 1.5-2.6 2.8-2.6M5.8 4.8v3M4.3 6.3h3" stroke="#EE7325" fill="none"/></svg>Persons</div>
    <div class="filter-row"><span>Filter Tags</span><span class="pill">Luxury</span><span class="pill">Comfortable</span></div>
    <span class="search-btn btn-line">Search</span>
  </form>
  <svg class="abs perk-tick" style="top:390px" width="16" height="16" viewBox="0 0 16 16"><circle cx="8" cy="8" r="7" fill="none" stroke="#EE7325" stroke-width="1.4"/><path d="M4.8 8.2l2.2 2.2 4.2-4.4" fill="none" stroke="#EE7325" stroke-width="1.4"/></svg>
  <div class="abs perk-title" style="top:418px">Competitive Pricing</div>
  <div class="abs perk-text" style="top:430px">Competitive costs, customized solutions.</div>
  <svg class="abs perk-tick" style="top:480px" width="16" height="16" viewBox="0 0 16 16"><circle cx="8" cy="8" r="7" fill="none" stroke="#EE7325" stroke-width="1.4"/><path d="M4.8 8.2l2.2 2.2 4.2-4.4" fill="none" stroke="#EE7325" stroke-width="1.4"/></svg>
</div>

<!-- Home screen, top -->
<div class="screen" style="left:465px; top:405px; height:520px;">
  <div class="abs page-band"></div>
  <div class="abs mini-brand"><span class="square"></span><span class="name">Tallowby</span></div>
  <svg class="abs search-ico" width="10" height="10" viewBox="0 0 10 10"><circle cx="4.2" cy="4.2" r="3.2" fill="none" stroke="#555" stroke-width="1"/><path d="M6.6 6.6L9.4 9.4" stroke="#555"/></svg>
  <div class="abs menu-dot"><svg width="17" height="17" viewBox="0 0 17 17"><path d="M5.5 6h6M5.5 8.5h6M5.5 11h6" stroke="#fff" stroke-width="1"/></svg></div>
  <h2 class="abs headline">Brighten your gathering<br>with Tallowby Hire.<br>The Velvet Privy</h2>
  <div class="abs photo hero-strip" role="img" aria-label="Luxury restroom trailer at an event"></div>
  <span class="abs chip" style="left:122px; top:108px">Available in 3 sizes</span>
  <span class="abs chip" style="left:100px; top:122px">Climate control inside</span>
  <span class="abs chip" style="left:130px; top:136px">Luxury Trailer Tours</span>
  <div class="abs finder-label">Find your Trailer</div>
  <form class="abs finder">
    <span class="field-label" style="top:8px">Where do you need your Trailers?</span>
    <div class="field" style="top:18px"><svg width="8" height="9" viewBox="0 0 8 10"><path d="M4 9.5S.8 6 .8 3.8a3.2 3.2 0 0 1 6.4 0C7.2 6 4 9.5 4 9.5z" fill="none" stroke="#EE7325" stroke-width="1"/><circle cx="4" cy="3.8" r="1.1" fill="#EE7325"/></svg>Los Angeles County</div>
    <span class="field-label" style="top:49px">When do you need?</span>
    <div class="field" style="top:59px"><svg width="8" height="8" viewBox="0 0 8 8"><rect x=".5" y="1.2" width="7" height="6.3" rx="1" fill="none" stroke="#EE7325"/><path d="M.5 3h7M2.3.3v1.6M5.7.3v1.6" stroke="#EE7325"/></svg>Pick a Date</div>
    <span class="field-label" style="top:92px">How much do you need?</span>
    <div class="field" style="top:102px"><svg width="8" height="8" viewBox="0 0 8 8"><circle cx="3.2" cy="2.4" r="1.8" fill="none" stroke="#EE7325"/><path d="M.4 7.6c.4-1.8 1.5-2.6 2.8-2.6M5.8 4.8v3M4.3 6.3h3" stroke="#EE7325" fill="none"/></svg>Persons</div>
    <div class="filter-row"><span>Filter Tags</span><span class="pill">Luxury</span><span class="pill">Comfortable</span></div>
    <span class="search-btn btn-line">Search</span>
  </form>
  <svg class="abs perk-tick" style="top:390px" width="16" height="16" viewBox="0 0 16 16"><circle cx="8" cy="8" r="7" fill="none" stroke="#EE7325" stroke-width="1.4"/><path d="M4.8 8.2l2.2 2.2 4.2-4.4" fill="none" stroke="#EE7325" stroke-width="1.4"/></svg>
  <div class="abs perk-title" style="top:418px">Competitive Pricing</div>
  <div class="abs perk-text" style="top:430px">Competitive costs, customized solutions.</div>
  <svg class="abs perk-tick" style="top:480px" width="16" height="16" viewBox="0 0 16 16"><circle cx="8" cy="8" r="7" fill="none" stroke="#EE7325" stroke-width="1.4"/><path d="M4.8 8.2l2.2 2.2 4.2-4.4" fill="none" stroke="#EE7325" stroke-width="1.4"/></svg>
</div>

<!-- Options screen -->
<div class="screen" style="left:702px; top:-10px; height:470px;">
  <div class="abs options-band"></div>
  <h2 class="abs section-title" style="top:16px">What do you need</h2>
  <article class="abs offer-card" style="top:33px;">
    <div class="offer-photo photo" role="img" aria-label="Two-stall restroom trailer for rent"></div>
    <div class="offer-badges"><span class="chip">1 Day Rate</span><span class="chip">1 Week Rate</span></div>
    <div class="offer-name">Rent Our Trailer</div>
    <div class="offer-feats"><span>◎ 2 Stalls</span><span>◎ AC Unit</span><span>◎ Vanity</span><span>◎ Music</span></div>
    <span class="offer-btn btn-fill">Order now</span>
  </article>
  <article class="abs offer-card" style="top:190px;">
    <div class="offer-photo photo" role="img" aria-label="Three-stall restroom trailer for sale"></div>
    <div class="offer-badges"><span class="chip">3 Stalls</span><span class="chip">For Sale</span></div>
    <div class="offer-name">Buy Our Trailer</div>
    <div class="offer-feats"><span>◎ 3 Stalls</span><span>◎ AC Unit</span><span>◎ Vanity</span><span>◎ Music</span></div>
    <span class="offer-btn btn-line">Order now</span>
  </article>
  <h2 class="abs feat-title">Featured Product</h2>
  <span class="abs explore btn-line">Explore more</span>
  <div class="abs area-label">Select Services Area</div>
  <div class="abs area-select"><svg width="7" height="8" viewBox="0 0 8 10"><path d="M4 9.5S.8 6 .8 3.8a3.2 3.2 0 0 1 6.4 0C7.2 6 4 9.5 4 9.5z" fill="none" stroke="#EE7325"/></svg>Los Angeles County<span style="margin-left:auto; margin-right:7px">⌄</span></div>
</div>

<!-- Product screen -->
<div class="screen" style="left:702px; top:507px; height:420px;">
  <div class="abs product-card"></div>
  <div class="abs photo product-photo" role="img" aria-label="Two-station luxury restroom trailer with blue steps"></div>
  <span class="abs price-tag">$ 150.00</span>
  <h3 class="abs product-name">Luxurious Trailler</h3>
  <div class="abs product-size">2 Station Trailer</div>
  <span class="abs book-btn btn-line">Book now</span>
  <div class="abs photo next-photo" role="img" aria-label="Restroom trailer interior"></div>
</div>

<!-- Contact screen -->
<div class="screen" style="left:936px; top:-20px; height:920px;">
  <div class="abs location-band"></div>
  <div class="abs location-photo" role="img" aria-label="Hand holding a phone showing a service area map"></div>
  <h2 class="abs loc-title">Our Location</h2>
  <div class="abs loc-sub">Visit Our Services Area</div>
  <span class="abs map-btn btn-line">View Maps</span>

  <div class="abs newsletter">
    <h3>Newsletter</h3>
    <p>Be the first one to know about discounts, offers and events</p>
    <div class="news-input">✉ Enter your email<span class="news-btn">Submit</span></div>
  </div>

  <div class="abs foot-brand"><span class="square"></span><span class="name">Tallowby Hire</span></div>
  <p class="abs foot-slogan">Brighten your gathering with Tallowby Hire. The Velvet Privy</p>

  <div class="abs contact-row" style="top:466px">
    <svg width="11" height="11" viewBox="0 0 12 12"><path d="M2.5 1h2l1 2.8-1.4 1a7 7 0 0 0 3 3l1-1.4 2.9 1v2c0 .6-.5 1-1 1A9.5 9.5 0 0 1 1.5 2c0-.5.4-1 1-1z" fill="none" stroke="#555"/></svg>
    <div><div class="lbl">Tel</div><div class="val">714-555-0182</div></div>
  </div>
  <div class="abs contact-row" style="top:495px">
    <svg width="11" height="11" viewBox="0 0 12 12"><rect x=".5" y="2" width="11" height="8" rx="1" fill="none" stroke="#555"/><path d="M.8 2.5L6 6.5l5.2-4" fill="none" stroke="#555"/></svg>
    <div><div class="lbl">Mail</div><div class="val">hello@tallowbyhire.com</div></div>
  </div>
  <div class="abs contact-row" style="top:525px">
    <svg width="11" height="12" viewBox="0 0 10 12"><path d="M5 11.5S1 7.3 1 4.6a4 4 0 0 1 8 0c0 2.7-4 6.9-4 6.9z" fill="none" stroke="#555"/><circle cx="5" cy="4.6" r="1.4" fill="none" stroke="#555"/></svg>
    <div><div class="lbl">Address</div><div class="val">Corvell Park, CA</div></div>
  </div>
  <div class="abs contact-row" style="top:553px">
    <svg width="11" height="11" viewBox="0 0 12 12"><rect x="3" y=".5" width="6" height="3.5" fill="none" stroke="#555"/><rect x=".5" y="4" width="11" height="5" rx="1" fill="none" stroke="#555"/><rect x="3" y="7.5" width="6" height="4" fill="#fff" stroke="#555"/></svg>
    <div><div class="lbl">Fax</div><div class="val">+1-714-555-0190</div></div>
  </div>

  <div class="abs accordion" style="top:584px">
    <div class="acc-row"><span>About</span><span>⌄</span></div>
    <div class="acc-row"><span>Support</span><span>⌄</span></div>
    <div class="acc-row"><span>Quick Links</span><span>⌄</span></div>
    <div class="acc-row"><span>FAQ</span><span>⌄</span></div>
    <div class="acc-row"><span>Support</span><span>⌄</span></div>
  </div>
  <ul class="abs foot-links">
    <li>About us</li><li>Contact</li><li>Privacy policy</li><li>Sitemap</li><li>Terms of Use</li>
  </ul>
  <div class="abs copyright">© 2024 Tallowby Hire. All Rights Reserved.</div>
</div>

</body>
</html>
```